Automotive component supplier needs a business card design

We need a business card design for our company called Velran Global Components Ltd based in the UK. We are a supplier of interior and exterior components to premium car manufacturers such as Corvel Ashby, Hadley Fenn, Marquist and Tavarelli. We would like to see a modern business card design that uses the colour blue.

Target Market(s)

Premium automotive car manufacturers.

Industry/Entity Type

Automotive

Contact Information for Business Card

Company Name : Velran Global Components Limited
Address: 17 Marlow Yard, Upper Heath, Warwick, CV31 8QL, United Kingdom
Web Address : www.velrancomponents-example.co.uk

Font styles to use
Other font styles liked:
• Helvetica

Colors
3176b5
0255a3
85acd3
cfdeed
cee9f5
85cae6
34a6d7
0692cd
9bcb3c

Requirements
Must have
• Clear company logo and a mixture of blue colours.
Nice to have
• A high quality modern image.
Should not have
• Multiple colours.

```html
<!DOCTYPE html>
<html lang="en">
<head>
<meta charset="utf-8">
<title>Velran Global Components – Business Card</title>
<link rel="stylesheet" href="https://fonts.googleapis.com/css2?family=Exo+2:wght@400;500;600;700&display=swap">
<style>
  :root {
    --backdrop: #e4e8ec;
    --card: #f3f6f8;
    --frame-blue: #1f68a8;
    --brand-blue: #0255a3;
    --name-blue: #0b5a9e;
    --accent-green: #9bcb3c;
    --title-green: #6f9f2a;
    --text-dark: #27333f;
    --icon-dark: #1d3f5e;
    --divider: #9fb3c6;
  }
  * { margin: 0; padding: 0; box-sizing: border-box; }
  html, body {
    width: 1200px; height: 969px; overflow: hidden;
    background: var(--backdrop);
    font-family: "Exo 2", Arial, sans-serif;
  }
  .canvas { position: relative; width: 1200px; height: 969px; }
  .business-card {
    position: absolute; left: 120px; top: 211px;
    width: 960px; height: 546px;
    background: var(--card);
    box-shadow: 0 10px 30px rgba(20, 40, 60, 0.15);
  }
  .card-frame {
    position: absolute; left: 4px; top: 4px; right: 0; bottom: 0;
    border: 21px solid var(--frame-blue);
    border-left-width: 19px; border-top-width: 19px;
  }
  .corner-accent {
    position: absolute; right: 0; top: 0;
    width: 32px; height: 32px;
    background: var(--accent-green);
    border-radius: 0 0 0 6px;
  }
  .brand {
    position: absolute; left: 86px; top: 230px;
    width: 380px;
    display: flex; align-items: center; gap: 14px;
  }
  .brand-square {
    width: 22px; height: 22px; flex: none; background: var(--accent-green);
  }
  .brand-name {
    color: var(--brand-blue);
    font-weight: 700;
    font-size: 31px; line-height: 1.1;
    letter-spacing: 0.5px;
    text-transform: uppercase;
    white-space: nowrap;
  }
  .divider {
    position: absolute; left: 498px; top: 99px;
    width: 2px; height: 406px; background: var(--divider);
  }
  .contact {
    position: absolute; left: 533px; top: 108px;
    width: 392px;
    color: var(--text-dark);
  }
  .person-name {
    color: var(--name-blue); font-weight: 700;
    font-size: 32px; letter-spacing: 1px; line-height: 40px;
  }
  .person-title {
    color: var(--title-green); font-weight: 500;
    font-size: 24px; line-height: 32px; margin-bottom: 20px;
  }
  .address { font-size: 23px; line-height: 33px; margin-bottom: 14px; white-space: nowrap; }
  .contact-list { list-style: none; }
  .contact-item {
    display: flex; align-items: center; gap: 12px;
    font-size: 23px; line-height: 37px;
    white-space: nowrap;
  }
  .contact-item.small { font-size: 19px; }
  .contact-icon { width: 22px; height: 22px; flex: none; fill: var(--icon-dark); }
</style>
</head>
<body>
<div class="canvas">
  <div class="business-card">
    <div class="card-frame"></div>
    <div class="corner-accent"></div>

    <div class="brand">
      <span class="brand-square"></span>
      <span class="brand-name">Velran<br>Global Components</span>
    </div>

    <div class="divider"></div>

    <div class="contact">
      <p class="person-name">DANIEL MARSH</p>
      <p class="person-title">CEO/Founder</p>
      <p class="address">17 Marlow Yard, Upper Heath<br>Warwick, CV31 8QL<br>United Kingdom</p>
      <ul class="contact-list">
        <li class="contact-item">
          <svg class="contact-icon" viewBox="0 0 24 24" aria-hidden="true"><path d="M6.6 10.8a15.2 15.2 0 0 0 6.6 6.6l2.2-2.2c.3-.3.7-.4 1-.2 1.1.4 2.3.6 3.6.6.6 0 1 .4 1 1V20c0 .6-.4 1-1 1A17 17 0 0 1 3 4c0-.6.4-1 1-1h3.5c.6 0 1 .4 1 1 0 1.3.2 2.5.6 3.6.1.3 0 .7-.2 1z"/></svg>
          <span>612 580 4471</span>
        </li>
        <li class="contact-item">
          <svg class="contact-icon" viewBox="0 0 24 24" aria-hidden="true"><path d="M7 1h10a2 2 0 0 1 2 2v18a2 2 0 0 1-2 2H7a2 2 0 0 1-2-2V3a2 2 0 0 1 2-2zm0 3v14h10V4zm5 15.2a1.2 1.2 0 1 0 0 2.4 1.2 1.2 0 0 0 0-2.4z"/></svg>
          <span>847 203 6195</span>
        </li>
        <li class="contact-item small">
          <svg class="contact-icon" viewBox="0 0 24 24" aria-hidden="true"><path d="M2 5h20v14H2zm2 2v.5l8 5 8-5V7zm0 2.8V17h16V9.8l-8 5z"/></svg>
          <span>daniel@velran-example.co.uk</span>
        </li>
        <li class="contact-item small">
          <svg class="contact-icon" viewBox="0 0 24 24" aria-hidden="true"><path d="M12 2a10 10 0 1 0 0 20 10 10 0 0 0 0-20zm6.9 6h-2.9a15.6 15.6 0 0 0-1.4-3.6A8 8 0 0 1 18.9 8zM12 4c.8 1.2 1.5 2.5 1.9 4h-3.8c.4-1.5 1.1-2.8 1.900-4zM4.3 14a8 8 0 0 1 0-4h3.4a16 16 0 0 0 0 4zm.8 2h2.9c.3 1.3.8 2.5 1.4 3.6A8 8 0 0 1 5.1 16zM8 8H5.1a8 8 0 0 1 4.3-3.6C8.8 5.5 8.3 6.7 8 8zm4 12c-.8-1.2-1.5-2.5-1.9-4h3.8c-.4 1.5-1.1 2.8-1.9 4zm2.3-6H9.7a14 14 0 0 1 0-4h4.6a14 14 0 0 1 0 4zm.3 5.6c.6-1.1 1.1-2.3 1.4-3.6h2.9a8 8 0 0 1-4.3 3.6zm1.7-5.6a16 16 0 0 0 0-4h3.4a8 8 0 0 1 0 4z"/></svg>
          <span>www.velrancomponents-example.co.uk</span>
        </li>
      </ul>
    </div>
  </div>
</div>
</body>
</html>
```